Coastline Premier Retreats Business Card Design

Design a business card for Coastline Premier Retreats. Look at the website for colors and reference. Card should have logo, name, title, office number, mobile number, email, URL and a tagline like, "Luxury Hotel & Resort Email Marketing" (This might change).

https://www.coastlinepremierretreats.example

The rest I will leave up to your imagination.

Contact Information for Business Card

Logo, name, title, office number, mobile number, email, URL and a tagline like, "Luxury Hotel & Resort Email Marketing" (This might change).

```html
<!DOCTYPE html>
<html lang="en">
<head>
<meta charset="utf-8">
<title>Coastline Premier Retreats – Business Card</title>
<link href="https://fonts.googleapis.com/css2?family=Montserrat:wght@400;500;700;800&display=swap" rel="stylesheet">
<style>
  :root {
    --backdrop: #262626;
    --ink: #0b0b0b;
    --paper: #ffffff;
    --accent: #f47a20;
    --text-dark: #1a1a1a;
    --text-light: #ffffff;
  }
  * { box-sizing: border-box; margin: 0; padding: 0; }
  html, body {
    width: 1200px; height: 900px; overflow: hidden;
    background: var(--backdrop);
    font-family: "Montserrat", Arial, sans-serif;
  }
  .stage {
    width: 1200px; height: 900px;
    display: flex; flex-direction: column;
    align-items: center; justify-content: center; gap: 56px;
  }
  .card {
    position: relative;
    width: 588px; height: 336px;
    border-radius: 22px;
    overflow: hidden;
    border-bottom: 7px solid var(--accent);
  }
  .card--front { background: var(--ink); }
  .card--back { background: var(--paper); }

  .brand {
    display: flex; align-items: center; gap: 14px;
    font-weight: 800; text-transform: uppercase;
    font-size: 32px; line-height: 1.05; letter-spacing: 1px;
  }
  .brand__mark {
    width: 18px; height: 18px; background: var(--accent); flex: none;
  }
  .card--front .brand { color: var(--text-light); position: absolute; left: 0; right: 0; top: 96px; justify-content: center; }
  .card--back .brand { color: var(--text-dark); position: absolute; left: 0; right: 0; top: 44px; justify-content: center; }

  .tagline {
    position: absolute; left: 0; right: 0; bottom: 44px;
    text-align: center; color: var(--accent);
    font-weight: 700; font-size: 15px;
  }

  .details {
    position: absolute; top: 158px; left: 0; right: 0;
    display: flex; justify-content: center; align-items: center;
  }
  .person { text-align: right; padding-right: 18px; }
  .person__name { color: var(--accent); font-weight: 800; font-size: 24px; }
  .person__title { color: var(--text-dark); font-size: 14px; font-weight: 500; }
  .divider { width: 2px; height: 88px; background: var(--accent); }
  .contacts { list-style: none; padding-left: 16px; }
  .contacts li {
    display: flex; align-items: center; gap: 9px;
    font-size: 13px; color: var(--text-dark); line-height: 21px;
    white-space: nowrap;
  }
  .contacts svg { width: 13px; height: 13px; fill: var(--accent); flex: none; }
  .address {
    position: absolute; left: 0; right: 0; bottom: 36px;
    text-align: center; font-size: 14px; color: var(--text-dark);
  }
</style>
</head>
<body>
<main class="stage">
  <section class="card card--front">
    <div class="brand"><span class="brand__mark"></span><span>Coastline<br>Premier Retreats</span></div>
    <p class="tagline">Luxury Hotel &amp; Resort Email Marketing</p>
  </section>

  <section class="card card--back">
    <div class="brand"><span class="brand__mark"></span><span>Coastline<br>Premier Retreats</span></div>
    <div class="details">
      <div class="person">
        <p class="person__name">Jonah Rivell</p>
        <p class="person__title">Owner</p>
      </div>
      <div class="divider"></div>
      <ul class="contacts">
        <li><svg viewBox="0 0 24 24"><path d="M6.6 10.8a15 15 0 0 0 6.6 6.6l2.2-2.2a1 1 0 0 1 1-.25 11.4 11.4 0 0 0 3.6.57 1 1 0 0 1 1 1V20a1 1 0 0 1-1 1A17 17 0 0 1 3 4a1 1 0 0 1 1-1h3.5a1 1 0 0 1 1 1c0 1.25.2 2.45.57 3.6a1 1 0 0 1-.25 1z"/></svg>555.201.4830 ext 37</li>
        <li><svg viewBox="0 0 24 24"><path d="M7 1h10a2 2 0 0 1 2 2v18a2 2 0 0 1-2 2H7a2 2 0 0 1-2-2V3a2 2 0 0 1 2-2zm0 3v14h10V4zm5 15.5a1.2 1.2 0 1 0 0 2.4 1.2 1.2 0 0 0 0-2.4z"/></svg>555.390.7716</li>
        <li><svg viewBox="0 0 24 24"><path d="M2 5h20v14H2zm2 2v.5l8 5 8-5V7zm0 2.9V17h16V9.9l-8 5z"/></svg>info@coastlinepremierretreats.example</li>
        <li><svg viewBox="0 0 24 24"><path d="M12 2a10 10 0 1 0 0 20 10 10 0 0 0 0-20zm-1 17.9A8 8 0 0 1 4.1 10l4.9 4.9v1a2 2 0 0 0 2 2zm6.9-2.5a2 2 0 0 0-1.9-1.4h-1v-3a1 1 0 0 0-1-1H8v-2h2a1 1 0 0 0 1-1V7h2a2 2 0 0 0 2-2v-.4a8 8 0 0 1 2.9 12.8z"/></svg>www.coastlinepremierretreats.example</li>
      </ul>
    </div>
    <p class="address">410 Harbor Way, Unit 9B Bayview, CA 90210</p>
  </section>
</main>
</body>
</html>
```